Create a memorable Stationary for Security Software Company

Velbrantix is the worldwide leader in securing the Internet. Making Internet communications and critical data secure, reliable and available everywhere has been and continues to be our ongoing vision. We are committed to staying focused on real customer needs and to developing new and innovative security solutions that redefine the security landscape.

Industry/Entity Type

Internet

Font styles to use
Serif
Sans Serif
Script

Colors
0792cd
33a6d7
85cae6

```html
<!DOCTYPE html>
<html lang="en">
<head>
<meta charset="utf-8">
<title>Velbrantix Stationery</title>
<link href="https://fonts.googleapis.com/css2?family=Arimo:wght@400;700&family=Questrial&family=Yellowtail&display=swap" rel="stylesheet">
<style>
  :root{
    --blue-deep:#0792cd;
    --blue-mid:#33a6d7;
    --blue-light:#85cae6;
    --backdrop:#e2e3e5;
    --paper:#ffffff;
    --ink:#1e1e1e;
  }
  *{margin:0;padding:0;box-sizing:border-box}
  html,body{width:1200px;height:900px;overflow:hidden;background:var(--backdrop)}
  body{position:relative;font-family:"Arimo",Arial,sans-serif;color:var(--ink)}
  .sheet{position:absolute;background:var(--paper);box-shadow:0 1px 3px rgba(0,0,0,.12);overflow:hidden}
  .block{position:absolute}
  .block--light{background:var(--blue-light)}
  .block--deep{background:var(--blue-deep)}
  .block--mid{background:var(--blue-mid)}
  .brand{position:absolute;display:flex;align-items:center;gap:6px;transform:translate(-50%,-50%);
    font-family:"Questrial",Arial,sans-serif;color:var(--blue-deep);white-space:nowrap}
  .brand__dot{border-radius:50%;background:var(--blue-deep);flex:none}
  .accent{font-family:"Questrial",Arial,sans-serif;color:var(--blue-deep)}

  /* letterhead */
  .letterhead{left:64px;top:103px;width:534px;height:691px}
  .contact-list{position:absolute;list-style:none;font-size:8.8px;line-height:10.6px}
  .contact-list li{display:flex;align-items:center;gap:4px}
  .contact-list svg{flex:none}
  .letterhead .contact-list{left:45px;top:187px}
  .recipient{position:absolute;left:45px;top:254px;font-size:9.2px;line-height:11px}
  .recipient__name{font-size:11px;font-weight:400;margin-bottom:5px;letter-spacing:.2px}
  .letter-body{position:absolute;left:45px;top:331px;width:448px;font-size:9.6px;line-height:15.7px;letter-spacing:-.1px}
  .letter-body p+p{margin-top:15.7px}
  .signoff{position:absolute;left:44px;top:522px;font-size:10px}
  .signature{position:absolute;left:44px;top:540px;font-family:"Yellowtail","Brush Script MT",cursive;font-size:34px;line-height:40px;white-space:nowrap}
  .signer{position:absolute;left:44px;top:588px;font-size:10.5px;line-height:13px}
  .letterhead .address{position:absolute;right:48px;top:653px;font-size:9.6px}

  /* envelope */
  .envelope-front{left:656px;top:102px;width:470px;height:236px}
  .envelope-front .address{position:absolute;right:24px;top:200px;font-size:7.6px;line-height:10px;text-align:right}
  .envelope-back{left:656px;top:354px;width:470px;height:236px}
  .envelope-back .flap{position:absolute;left:0;top:0}
  .envelope-back .site{position:absolute;left:0;width:100%;top:209px;text-align:center;font-size:8.4px}

  /* business cards */
  .card-front{left:656px;top:663px;width:226px;height:129px}
  .card-front .footer-band{position:absolute;left:0;bottom:0;width:100%;height:16px;background:var(--blue-mid);
    color:#fff;font-family:"Questrial",Arial,sans-serif;font-size:5.4px;text-align:center;line-height:16px}
  .card-back{left:900px;top:663px;width:226px;height:129px}
  .card-back .title{position:absolute;right:10px;top:21px;text-align:right;color:#fff;font-weight:700;font-size:8px;line-height:8px}
  .card-back .title span{display:block;font-weight:400;font-size:5.6px;line-height:7px}
  .card-back .contact-list{left:15px;top:93px;font-size:5.8px;line-height:8px}
  .card-back .address{position:absolute;right:10px;top:101px;font-size:5.8px;line-height:8px;text-align:right}
</style>
</head>
<body>

<!-- Letterhead -->
<section class="sheet letterhead">
  <div class="block block--light" style="left:0;top:38px;width:43px;height:68px"></div>
  <div class="brand" style="left:117px;top:73px;font-size:17px"><span class="brand__dot" style="width:14px;height:14px"></span>Velbrantix</div>
  <div class="block block--deep" style="left:189px;top:38px;width:345px;height:68px"></div>

  <ul class="contact-list accent">
    <li><svg width="8" height="8" viewBox="0 0 8 8"><rect width="8" height="8" fill="var(--blue-mid)"/><path d="M2 1.6l1 1-0.6.7a4 4 0 0 0 2.3 2.3l.7-.6 1 1-.8.8C3.6 6.6 1.4 4.4 1.2 2.4z" fill="#fff"/></svg>000 000 0000</li>
    <li><svg width="8" height="8" viewBox="0 0 8 8"><rect width="8" height="8" fill="var(--blue-mid)"/><rect x="1.5" y="2.3" width="5" height="3.4" fill="none" stroke="#fff" stroke-width=".7"/><path d="M1.5 2.3l2.5 2 2.5-2" fill="none" stroke="#fff" stroke-width=".7"/></svg>hello@velbrantix.net</li>
    <li><svg width="8" height="8" viewBox="0 0 8 8"><rect width="8" height="8" fill="var(--blue-mid)"/><circle cx="4" cy="4" r="2.5" fill="none" stroke="#fff" stroke-width=".7"/><path d="M1.5 4h5M4 1.5v5" stroke="#fff" stroke-width=".5"/></svg>www.velbrantix.net</li>
  </ul>

  <div class="recipient">
    <p class="recipient__name">ELLIS MARROW</p>
    <p>Street Name,City Name.</p>
    <p>Zip Coad 0000</p>
  </div>

  <div class="letter-body">
    <p>Lorem Ipsum is simply dummy text of the printing and typesetting industry. Lorem Ipsum has been the industry’s standard dummy text ever since the 1500s, when an unknown printer took a galley of type and scrambled it to make a type specimen book. It has survived not only five centuries, but also the leap into electronic typesetting, remaining essentially unchanged. It was popularised in the 1960s with the release of Transfera sheets containing Lorem Ipsum passages, and more recently with desktop publishing software like Quillpage Layout including versions of Lorem Ipsum.</p>
    <p>It is a long established fact that a reader will be distracted by the readable content of a page when looking at its layout. The point of using Lorem Ipsum is that it has a more-or-less normal distribution of letters, as opposed to using ’Content here, content here’,</p>
  </div>

  <p class="signoff">Regards,</p>
  <p class="signature">Dana Hollis</p>
  <div class="signer"><p>Dana Hollis</p><p>General Maneger</p></div>
  <p class="address accent">0000 Your Address,2nd Ste. Brightvale, Region 1234</p>
</section>

<!-- Envelope front -->
<section class="sheet envelope-front">
  <div class="block block--light" style="left:0;top:20px;width:34px;height:57px"></div>
  <div class="brand" style="left:96px;top:48px;font-size:14px"><span class="brand__dot" style="width:11px;height:11px"></span>Velbrantix</div>
  <div class="block block--deep" style="left:158px;top:20px;width:312px;height:57px"></div>
  <p class="address accent">0000 Your Address,2nd Ste.<br>Brightvale, Region 1234</p>
  <div class="block block--deep" style="right:0;top:202px;width:6px;height:17px"></div>
</section>

<!-- Envelope back -->
<section class="sheet envelope-back">
  <svg class="flap" width="470" height="70" viewBox="0 0 470 70">
    <path d="M1 0 L8 60 Q9 66 16 66 L454 66 Q461 66 462 60 L469 0" fill="none" stroke="#c9cbce" stroke-width="1"/>
  </svg>
  <div class="brand" style="left:234px;top:34px;font-size:11px"><span class="brand__dot" style="width:9px;height:9px"></span>Velbrantix</div>
  <p class="site accent">www.velbrantix.net</p>
</section>

<!-- Business card front -->
<section class="sheet card-front">
  <div class="brand" style="left:112px;top:57px;font-size:15px"><span class="brand__dot" style="width:12px;height:12px"></span>Velbrantix</div>
  <div class="footer-band">www.velbrantix.net</div>
</section>

<!-- Business card back -->
<section class="sheet card-back">
  <div class="block block--light" style="left:0;top:16px;width:21px;height:27px"></div>
  <div class="brand" style="left:50px;top:30px;font-size:8px"><span class="brand__dot" style="width:6px;height:6px"></span>Velbrantix</div>
  <div class="block block--deep" style="left:79px;top:16px;width:147px;height:27px"></div>
  <p class="title">Employee Name<span>Principal Consultant</span></p>
  <div class="block block--deep" style="left:0;top:93px;width:3px;height:22px"></div>
  <ul class="contact-list accent">
    <li><svg width="6" height="6" viewBox="0 0 8 8"><rect width="8" height="8" fill="var(--blue-mid)"/></svg>000 000 0000</li>
    <li><svg width="6" height="6" viewBox="0 0 8 8"><rect width="8" height="8" fill="var(--blue-mid)"/></svg>hello@velbrantix.net</li>
    <li><svg width="6" height="6" viewBox="0 0 8 8"><rect width="8" height="8" fill="var(--blue-mid)"/></svg>www.velbrantix.net</li>
  </ul>
  <p class="address accent">0000 Your Address,2nd Ste.<br>Brightvale, Region 1234</p>
</section>

</body>
</html>
```